Business Card Design for Software Development Company

I am looking for a business card design the incorporates my new logo (attached below).

Key information to include:
Name: Martin Quelbrook
Title: CEO
Email: martin@brightwellcivic.example
Phone: 555-218-9403
Website: www.brightwellcivic.example

NOTE: This design should be easy to edit so that we can order cards for different members of our team.

```html
<!DOCTYPE html>
<html lang="en">
<head>
<meta charset="utf-8">
<title>Brightwell Labs — Business Card</title>
<link rel="stylesheet" href="https://fonts.googleapis.com/css2?family=Josefin+Sans:wght@400;600;700&display=swap">
<style>
  :root {
    --navy: #333a52;
    --teal: #0faa94;
    --peach: #f5c08c;
    --orange: #ec7a22;
    --red: #a52024;
    --paper: #ffffff;
    --stage: #e6e7ea;
    --ink: #2c3148;
    --rule: #8a8d99;
  }
  * { margin: 0; padding: 0; box-sizing: border-box; }
  html, body { width: 1200px; height: 900px; overflow: hidden; }
  body {
    background: var(--stage);
    font-family: "Josefin Sans", sans-serif;
    position: relative;
  }
  .card {
    position: absolute;
    left: 280px;
    width: 640px;
    height: 366px;
    border-radius: 28px;
    overflow: hidden;
    box-shadow: 0 10px 28px rgba(0,0,0,.18);
  }
  .card--front { top: 50px; background: var(--navy); }
  .card--back { top: 470px; background: var(--paper); }

  .card__artwork {
    position: absolute;
    inset: 0;
    clip-path: polygon(45% 0, 100% 0, 100% 85%);
    background: linear-gradient(160deg, var(--teal) 0%, var(--peach) 50%, var(--orange) 78%, var(--red) 100%);
  }
  .card--back .card__artwork { opacity: .16; }

  .brand {
    position: absolute;
    left: 70px;
    display: flex;
    flex-direction: column;
    align-items: flex-end;
  }
  .brand__row { display: flex; align-items: center; gap: 14px; }
  .brand__dot {
    width: 28px; height: 28px; border-radius: 50%;
    background: var(--orange);
  }
  .brand__name {
    font-weight: 700;
    font-size: 48px;
    letter-spacing: -0.5px;
    line-height: 1;
  }
  .brand__tagline {
    margin-top: 6px;
    font-size: 8.5px;
    font-weight: 600;
    letter-spacing: 0.6px;
    text-transform: uppercase;
  }
  .card--front .brand { top: 200px; }
  .card--front .brand__name,
  .card--front .brand__tagline { color: var(--paper); }

  .card--back .brand { top: 120px; }
  .card--back .brand__name,
  .card--back .brand__tagline { color: var(--ink); }

  .contact {
    position: absolute;
    left: 60px;
    right: 46px;
    bottom: 40px;
  }
  .contact__name {
    color: var(--orange);
    font-weight: 600;
    font-size: 19px;
    letter-spacing: 1.2px;
    text-transform: uppercase;
  }
  .contact__role-row { display: flex; align-items: center; gap: 12px; margin-top: 4px; }
  .contact__role { color: var(--ink); font-size: 19px; }
  .contact__rule { flex: 1; height: 1px; background: var(--rule); }
  .contact__details {
    margin-top: 10px;
    color: var(--ink);
    font-size: 13.5px;
    letter-spacing: 0.3px;
    white-space: nowrap;
  }
  .contact__label { color: var(--teal); font-weight: 600; }
  .contact__sep { color: var(--teal); margin: 0 7px; }
</style>
</head>
<body>

  <section class="card card--front" aria-label="Card front">
    <div class="card__artwork" role="img" aria-label="Angular decorative colour artwork in teal, peach, orange and red"></div>
    <div class="brand">
      <div class="brand__row">
        <span class="brand__dot"></span>
        <span class="brand__name">Brightwell Labs</span>
      </div>
      <span class="brand__tagline">A division of Brightwell Civic</span>
    </div>
  </section>

  <section class="card card--back" aria-label="Card back">
    <div class="card__artwork" role="img" aria-label="Faded angular decorative colour artwork"></div>
    <div class="brand">
      <div class="brand__row">
        <span class="brand__dot"></span>
        <span class="brand__name">Brightwell Labs</span>
      </div>
      <span class="brand__tagline">A division of Brightwell Civic</span>
    </div>

    <div class="contact">
      <p class="contact__name">Martin Quelbrook</p>
      <div class="contact__role-row">
        <span class="contact__role">CEO</span>
        <span class="contact__rule"></span>
      </div>
      <p class="contact__details">
        <span class="contact__label">P.</span> 555-218-9403<span class="contact__sep">|</span>martin@brightwellcivic.example<span class="contact__sep">|</span>www.brightwellcivic.example
      </p>
    </div>
  </section>

</body>
</html>
```